Business Card Design Project

We are a construction company in Orange County, CA. We need a two sided business card. We would like the back to be our logo with web URL. Front should included Name, title, address, phone, fax and email address.

our address is
627 West Dorrance Blvd, Suite 308
Anaheim, CA 92718

Our logo files are attached.

Construction

```html
<!DOCTYPE html>
<html lang="en">
<head>
<meta charset="utf-8">
<title>Strata Business Card</title>
<link rel="stylesheet" href="https://fonts.googleapis.com/css2?family=Source+Sans+3:wght@400;600;700;900&display=swap">
<style>
  :root {
    --page-bg: #e9e6e1;
    --card-white: #ffffff;
    --brand-blue: #174a7c;
    --ink-grey: #4a4a4a;
    --swoosh-dark: #1e1e1e;
    --swoosh-mid: #8a8a8a;
    --back-light: #7a7a7a;
    --back-dark: #3e3e3e;
    --back-url: #d8d8d8;
  }
  * { margin: 0; padding: 0; box-sizing: border-box; }
  html, body { width: 1200px; height: 404px; overflow: hidden; }
  body {
    background: var(--page-bg);
    font-family: "Source Sans 3", sans-serif;
    position: relative;
  }
  .card {
    position: absolute;
    top: 50px;
    width: 525px;
    height: 300px;
    overflow: hidden;
    box-shadow: 0 2px 6px rgba(0,0,0,.25);
  }
  .card-front { left: 55px; background: var(--card-white); }
  .card-back {
    left: 620px;
    background: radial-gradient(ellipse at 50% 50%, var(--back-light) 0%, var(--back-dark) 85%);
  }
  .wordmark {
    font-weight: 900;
    letter-spacing: -1px;
    line-height: 1;
  }
  .tagline {
    font-weight: 600;
    letter-spacing: 3.2px;
    font-size: 11.5px;
    line-height: 1;
  }
  .card-front .wordmark {
    position: absolute; left: 36px; top: 44px;
    font-size: 82px; color: var(--brand-blue);
  }
  .card-front .tagline {
    position: absolute; left: 38px; top: 113px;
    color: var(--brand-blue);
  }
  .person {
    position: absolute; left: 38px; top: 166px;
    font-size: 17px; color: var(--brand-blue);
  }
  .person .name { font-weight: 700; }
  .address {
    position: absolute; left: 38px; top: 203px;
    font-size: 13px; line-height: 18px; color: var(--ink-grey);
  }
  .wave { position: absolute; left: 0; top: 0; }
  .contact {
    position: absolute; right: 20px; top: 218px;
    list-style: none; color: #fff; font-size: 13px; line-height: 17.5px;
  }
  .contact li { display: flex; justify-content: flex-end; align-items: center; gap: 5px; }
  .contact svg { width: 11px; height: 11px; fill: #fff; }
  .card-back .logo-block {
    position: absolute; left: 0; right: 0; top: 82px; text-align: center;
  }
  .card-back .wordmark { font-size: 82px; color: #fff; }
  .card-back .tagline { color: #fff; margin-top: -12px; padding-left: 3px; }
  .card-back .url {
    position: absolute; left: 0; right: 0; top: 192px; text-align: center;
    color: var(--back-url); font-size: 14px; letter-spacing: 2.5px;
  }
</style>
</head>
<body>
  <section class="card card-front">
    <svg class="wave" width="525" height="300" viewBox="0 0 525 300">
      <defs>
        <linearGradient id="swooshFill" x1="0" x2="1" y1="0" y2="0">
          <stop offset="0" stop-color="var(--swoosh-dark)"/>
          <stop offset="0.55" stop-color="var(--swoosh-mid)"/>
          <stop offset="1" stop-color="var(--swoosh-dark)"/>
        </linearGradient>
      </defs>
      <path d="M0,272 C160,300 330,225 525,166 L525,300 L0,300 Z" fill="var(--brand-blue)"/>
      <path d="M0,238 C110,300 300,240 525,156 L525,162 C300,248 120,300 0,246 Z" fill="url(#swooshFill)"/>
      <path d="M40,262 C170,290 330,232 525,164 L525,168 C330,240 170,296 40,262 Z" fill="var(--swoosh-dark)"/>
    </svg>
    <div class="wordmark">STRATA</div>
    <div class="tagline">BUILD • MANAGE • DELIVER</div>
    <p class="person"><span class="name">Your Name,</span> Title</p>
    <p class="address">627 West Dorrance Blvd<br>Suite 308, Anaheim, CA&nbsp; 92718</p>
    <ul class="contact">
      <li><svg viewBox="0 0 12 12"><path d="M2.5 0.5 L4.5 3 L3.3 4.3 C4 5.9 5.9 7.8 7.6 8.6 L8.9 7.4 L11.5 9.4 L10 11.5 C5 11 1 6.8 0.5 2 Z"/></svg>01-555-0142</li>
      <li><svg viewBox="0 0 12 12"><path d="M3 0.5 H9 V4 H3 Z M1 4.5 H11 V10 H1 Z M3 10.5 H9 V11.5 H3 Z"/></svg>01-555-0143</li>
      <li><svg viewBox="0 0 12 12"><path d="M0.5 2.5 H11.5 V9.5 H0.5 Z"/></svg>info@strataco.com</li>
      <li><svg viewBox="0 0 12 12"><circle cx="6" cy="6" r="5.5"/></svg>www.strataco.com</li>
    </ul>
  </section>

  <section class="card card-back">
    <div class="logo-block">
      <div class="wordmark">STRATA</div>
      <div class="tagline">BUILD • MANAGE • DELIVER</div>
    </div>
    <p class="url">www.strataco.com</p>
  </section>
</body>
</html>
```